Bulldog themed background for Real Estate Purchase Letter

I need a phantom background or watermark on a standard 8 1/2" x 11" paper. I am going to put a letter over the background. I want a bulldog theme that is cute, funny and original. This letter is for a real estate project and we want to capture the person sub-consciously . Attached is my personal dogs. If you want to use them you can but not required. I have attached the letter that I am trying to emulate. I want bulldogs not horses.

Target Market(s)

45 years old and higher

Industry/Entity Type

Real Estate

Font styles to use
Serif
Sans Serif

Colors

Designer to choose colors to be used in the design.

Requirements
Must have
• fun, happiness, reassuring,
Should not have
• violence, negativity, unhappy

```html
<!DOCTYPE html>
<html lang="en">
<head>
<meta charset="utf-8">
<title>Letterhead – Whitfield Homes</title>
<link href="https://fonts.googleapis.com/css2?family=Montserrat:wght@400;500;700&display=swap" rel="stylesheet">
<style>
  :root {
    --backdrop: #d9d9d9;
    --paper: #ffffff;
    --ink: #2b2b2b;
    --ink-strong: #1c1c1c;
    --brand-blue: #2b6690;
    --watermark-cream: #f3ead4;
    --watermark-light: #fbf6e6;
    --gold-dark: #b88a3a;
    --gold-light: #f2d77a;
  }
  * { box-sizing: border-box; margin: 0; padding: 0; }
  html, body {
    width: 1200px; height: 1200px; overflow: hidden;
    background: var(--backdrop);
    font-family: "Montserrat", sans-serif;
    color: var(--ink);
  }
  .letter-page {
    position: absolute;
    left: 159px; top: 30px;
    width: 881px; height: 1140px;
    background: var(--paper);
    overflow: hidden;
  }
  .watermark-art {
    position: absolute;
    left: 3px; top: 92px; width: 878px; height: 1048px;
    background: radial-gradient(ellipse 55% 50% at 58% 52%, var(--watermark-light) 0%, var(--watermark-cream) 60%, rgba(243,234,212,0) 100%);
    opacity: 0.55;
  }
  .recipient {
    position: absolute; left: 76px; top: 78px;
    font-size: 15.5px; line-height: 20.5px; font-weight: 400;
  }
  .recipient .owner-name { color: var(--brand-blue); }
  .agent-title {
    position: absolute; right: 79px; top: 119px;
    font-size: 15.5px; line-height: 20.5px; letter-spacing: 0.2px;
  }
  .letter-body {
    position: absolute; left: 76px; top: 368px; width: 730px;
    font-size: 13.6px; line-height: 28px;
  }
  .letter-body p + p { margin-top: 28.5px; }
  .closing {
    position: absolute; left: 76px; top: 834px;
    font-size: 13.6px;
  }
  .signature {
    position: absolute; left: 76px; top: 904px;
  }
  .signature .signer-name {
    font-size: 18.6px; font-weight: 700; color: var(--ink-strong); line-height: 24px;
  }
  .signature .signer-phone { font-size: 13.5px; line-height: 20px; }
  .postscript {
    position: absolute; left: 76px; top: 1008px; width: 740px;
    font-size: 17px; line-height: 25px;
  }
  .footer-rule {
    position: absolute; left: 76px; top: 1081px; width: 726px; height: 2px;
    background: linear-gradient(90deg, var(--gold-dark), var(--gold-light) 45%, var(--gold-dark));
  }
  .brand-mark {
    position: absolute; right: 79px; top: 960px;
    display: flex; align-items: center; gap: 8px;
    font-size: 17px; font-weight: 500; color: var(--brand-blue);
  }
  .brand-mark .brand-square {
    width: 14px; height: 14px; background: var(--brand-blue);
  }
</style>
</head>
<body>
  <main class="letter-page">
    <div class="watermark-art" role="img" aria-label="Faint cream watermark of a friendly cartoon bulldog leaning on a house roof"></div>

    <address class="recipient" style="font-style:normal">
      <div><span class="owner-name">MR. OUTTA STATEOWNER</span> -&nbsp; Non PA Address</div>
      <div>12345 Main Street</div>
      <div>MAPLEWOOD FL 34000-1200</div>
    </address>
    <div class="agent-title">LICENSED REAL STATE AGENT</div>

    <section class="letter-body">
      <p>This is a sample letter that has been placed to demonstrate typing remat (Your Company). letterhead design. When positioned properly, it will serve to work in harmony with all other elements letterhead. This letterhead design is meant to project an image</p>
      <p>This letterhead design is meant project an image of professionalism reliability. By using simple aligen we have created a very spacious feeling. The simplicity suggest&nbsp; rengththe spaciousnes contributes haesthetics the layout. These basic qualities along with the (Your Company)</p>
      <p>look and helps reinforce the (Your Company) brand. letterhead design is meant to project an image design. When positioned properly, it will serve to work in harmony all the other elements letterhead. sionalism and reliability.</p>
      <p>This letterhead design is based on the (Form of your logo) form (Your Company) logo. Each stationery we have created a very spacious feeling. The simplicity suggests strength the spaciousnes contribute part of the (Form of your logo).</p>
    </section>

    <div class="closing">Sincearly,</div>

    <div class="signature">
      <div class="signer-name">Dana Whitfield</div>
      <div class="signer-phone">(xxx) XXXX-XXXXX</div>
    </div>

    <div class="brand-mark">
      <span class="brand-square"></span>
      <span class="brand-name">Whitfield Homes</span>
    </div>

    <p class="postscript">P.S.&nbsp; If you would like to e- mail me information and pictures of your property, Please Send them to dana@whitfieldmail.com</p>

    <div class="footer-rule"></div>
  </main>
</body>
</html>
```